Build a landing page to promote a service (dialler consultation and support).

We are a call centre consultation firm and we need a landing page to promote a service. The service is Tormalux dialler consultation and support.
If you do not know what Tormalux is, please do some quick "Zorvex" research for more information.
The landing page will be promoted with a paid advertisement, so we want something that is simple, and explains exactly what service we offer.
There are two objectives for the landing page:
1) A "call to action" which directs the user to a contact page, including a form plus all of our contact details.
2) A form for them viewers to enter their details to get a "FREE" quote for their project. This form should be placed on the main page.
Notes:
The call to action will require the viewer to enter their name, email, phone number as well as a description of their request. There will also need to be a drop down menu for the type of quote. This menu should have the following options:
1) Tormalux support
2) Tormalux hosting
3) Tormalux customisation
4) Other
We need 2 pages in total:
1) Main landing page
This is the home page. It will need to clearly indicate our services and our key selling features.
Services:
* Tormalux support
* Tormalux hosting
* Tormalux customisation
Key Selling Features:
* Australian based
* PCI complaint
* 10+ years of dialler and call centre experience
* we run a sister company which is a highly reputable 40 seat call centre, so we know first hand about call centre technology.
The main landing page will have an "about us" section with a few paragraphs about how we got started.
-------------------------------------------------------------------------
2) Contact page
All of our contact details will live on this page, as well as a contact form.
Other notes:
We will be self hosting the landing page.
We already have a domain name.
The design must be clean and incorporate our logo, as well as it's colours. (Logo attached)
We want a fully function HTML landing page, not just a "PSD" design.
The page must be mobile optimised.
Anyone using Tormalux software.

```html
<!DOCTYPE html>
<html lang="en">
<head>
<meta charset="utf-8">
<title>Dialwise – Tormalux Dialler Consultation and Support</title>
<link href="https://fonts.googleapis.com/css2?family=Mulish:wght@400;600;700;800&display=swap" rel="stylesheet">
<style>
:root{
  --stage:#ababab;
  --white:#ffffff;
  --blue:#1b7cc4;
  --blue-deep:#1565b5;
  --teal:#20ad8e;
  --teal-soft:#2bb3a0;
  --navy:#102466;
  --ink:#2a2f3a;
  --muted:#5d6470;
  --grey-band:#ececec;
  --photo-warm:#b79a82;
  --photo-cool:#6f8aa6;
}
*{box-sizing:border-box;margin:0;padding:0}
html,body{width:861px;height:1200px;overflow:hidden;background:var(--stage);font-family:'Mulish',sans-serif;color:var(--ink)}
.stage{position:absolute;left:0;top:0;width:1076px;height:1500px;transform:scale(.8);transform-origin:0 0}
.page{position:absolute;width:458px;background:var(--white);overflow:hidden}
.page--home{left:69px;top:22px;height:1455px}
.page--contact{left:554px;top:24px;height:505px}
.block{position:absolute;left:0;width:458px}
.abs{position:absolute}

.nav{top:0;height:34px;background:var(--white)}
.brand{position:absolute;left:70px;top:7px;display:flex;align-items:center;gap:5px;font-weight:700;font-size:11px;color:var(--blue)}
.brand-dot{width:21px;height:21px;border-radius:50%;background:var(--blue)}
.menu{position:absolute;top:0;height:34px;display:flex;font-size:6.5px;color:var(--navy)}
.menu span{padding:0 8px;line-height:34px}
.menu .active{background:#f0f0f0;color:var(--blue)}
.page--contact .menu .active{background:#f0f0f0}

.photo{background:linear-gradient(120deg,var(--photo-cool),var(--photo-warm) 60%,#d9c5b3)}
.hero-panel{left:59px;top:55px;width:168px;height:101px;background:rgba(32,173,170,.88);color:var(--white);padding:15px 18px}
.hero-panel h1{font-weight:400;font-size:13px;line-height:1.05}
.hero-panel h1 b{display:block;font-weight:400;font-size:17px}
.hero-panel p{font-size:6.5px;line-height:1.25;opacity:.85;margin-top:3px}
.btn-ghost{display:inline-block;border:1px solid currentColor;border-radius:10px;font-size:5.5px;font-weight:800;padding:4px 13px;letter-spacing:.2px}
.hero-panel .btn-ghost{margin-top:7px}
.arrow{width:10px;height:22px}
.scroll-tab{width:26px;height:14px;background:var(--white);border-radius:13px 13px 0 0;left:216px}
.scroll-mouse{width:7px;height:11px;border:1px solid #888;border-radius:4px;left:9px;top:2px}

.section-title{text-align:center;font-size:12px;font-weight:600}
.h-service{font-size:11px;color:var(--blue);font-weight:600}
.body-text{font-size:5.8px;line-height:1.4;color:var(--muted)}
.btn-outline{color:var(--blue);border:1px solid var(--blue);border-radius:10px;font-size:5.5px;font-weight:800;padding:5px 14px;display:inline-block}

.features{top:426px;height:176px;background:linear-gradient(135deg,var(--teal) 0%,#1c9cb0 50%,var(--blue-deep) 100%);color:var(--white)}
.feature-row{left:69px;top:43px;display:flex;gap:2px}
.feature{width:78px;height:103px;background:rgba(255,255,255,.1);text-align:center;padding:10px 6px;font-size:6.3px;line-height:1.25}
.feature svg{display:block;margin:0 auto 6px}
.feature--small{font-size:5.5px}

.circle-photo{border-radius:50%;border:4px solid var(--teal);padding:4px;background:var(--white)}
.circle-photo div{width:100%;height:100%;border-radius:50%}

.quote{top:1158px;height:157px;background:linear-gradient(135deg,#1d8fd2,var(--blue-deep) 60%,#1a5bb0);color:var(--white)}
.field{position:absolute;background:var(--white);font-size:5px;color:#666;padding:3px 6px;height:16px}
.submit{background:#111;color:var(--white);border-radius:9px;font-size:5.5px;font-weight:800;text-align:center;line-height:18px}

.footer{background:var(--navy);color:var(--white)}
.f-brand{display:flex;flex-direction:column;align-items:center;gap:5px;font-size:10px;font-weight:600;letter-spacing:.5px}
.f-brand .brand-dot{background:var(--white);width:22px;height:22px}
.f-col h4{font-size:6.5px;font-weight:600;margin-bottom:5px}
.f-col p{font-size:5px;opacity:.8;line-height:2.1;display:flex;align-items:center;gap:3px}
.bar{background:var(--teal-soft);color:rgba(255,255,255,.8);font-size:4.5px;text-align:center;line-height:22px}
.bar .tag{position:absolute;right:10px;top:0}

.contact-label{font-size:6.5px;color:var(--teal);font-weight:600}
.contact-val{font-size:7px;color:var(--ink);line-height:1.35;margin-top:2px}
.quote-box{left:193px;top:29px;width:198px;height:119px;background:linear-gradient(135deg,var(--teal),var(--blue-deep));color:var(--white);padding:11px 12px}
.quote-box h3{font-size:7.5px;font-weight:800}
.qfield{position:absolute;background:var(--white);font-size:4px;color:#666;padding:2px 4px;height:10px}
</style>
</head>
<body>
<div class="stage">

<!-- HOME PAGE -->
<main class="page page--home">
  <header class="block nav">
    <div class="brand"><span class="brand-dot"></span>Dialwise</div>
    <nav class="menu" style="left:180px"><span class="active">Home</span><span>About Us</span><span>Our Services</span><span>Blogs</span><span>Contact Us</span></nav>
  </header>

  <section class="block photo" style="top:34px;height:222px" role="img" aria-label="Call centre agents wearing headsets working at computers">
    <div class="abs hero-panel">
      <h1>Tormalux Dedicated<b>Hosting Services</b></h1>
      <p>Maecenas aliquet velit vel turpis Mauris neque metus malesuada nec ultri</p>
      <span class="btn-ghost">READ MORE</span>
    </div>
    <svg class="abs arrow" style="left:28px;top:86px" viewBox="0 0 10 22"><path d="M9 1 1 11l8 10" fill="none" stroke="#fff" stroke-width="1.2"/></svg>
    <svg class="abs arrow" style="left:418px;top:86px" viewBox="0 0 10 22"><path d="M1 1l8 10-8 10" fill="none" stroke="#fff" stroke-width="1.2"/></svg>
    <div class="abs scroll-tab" style="top:208px"><div class="abs scroll-mouse"></div></div>
  </section>

  <section class="block" style="top:256px;height:170px">
    <div class="abs" style="left:66px;top:27px;width:165px;height:110px;background:linear-gradient(135deg,#e8f3fb,#e5f6f1)" role="img" aria-label="Line illustration of support agents with headsets and chat bubbles"></div>
    <div class="abs" style="left:245px;top:36px;width:165px">
      <h2 style="font-size:13px;font-weight:600">About Dialwise</h2>
      <p class="body-text" style="margin-top:6px">Maecenas aliquet velit vel turpis Mauris neque metus malesuada nec ultricies sit amet porttitor</p>
      <p class="body-text" style="margin-top:6px">Aed nulla In ullamcorper est eget tempor cursus neque mi consectetuer mi a ultricies massa est sed nisl Class aptent taciti sociosqu ad litora torquent per</p>
      <span class="btn-outline" style="margin-top:10px">READ MORE</span>
    </div>
  </section>

  <section class="block features">
    <h2 class="section-title" style="position:absolute;top:16px;width:100%;font-weight:500">Key Selling Features</h2>
    <div class="abs feature-row">
      <div class="feature"><svg width="22" height="20" viewBox="0 0 22 20"><circle cx="11" cy="10" r="8" fill="none" stroke="#fff"/><circle cx="11" cy="10" r="2" fill="#fff"/></svg>Australian<br>based</div>
      <div class="feature"><svg width="22" height="20" viewBox="0 0 22 20"><path d="M4 13V10a7 7 0 0 1 14 0v3" fill="none" stroke="#fff"/><rect x="3" y="11" width="3" height="6" rx="1" fill="none" stroke="#fff"/><rect x="16" y="11" width="3" height="6" rx="1" fill="none" stroke="#fff"/></svg>10+ years of dialler and call centre experience</div>
      <div class="feature"><svg width="22" height="20" viewBox="0 0 22 20"><circle cx="11" cy="10" r="5" fill="none" stroke="#fff"/><circle cx="11" cy="10" r="8.5" fill="none" stroke="#fff" stroke-dasharray="3 2"/></svg>PCI Complaint</div>
      <div class="feature feature--small"><svg width="22" height="20" viewBox="0 0 22 20"><circle cx="11" cy="9" r="7" fill="none" stroke="#fff"/><circle cx="11" cy="9" r="2.5" fill="none" stroke="#fff"/></svg>We run a sister company which is a highly reputable 40 seat call centre, so we know first hand about call centre technology.</div>
    </div>
  </section>

  <section class="block" style="top:602px;height:199px">
    <h2 class="section-title" style="position:absolute;top:20px;width:100%;font-weight:500">Our Services</h2>
    <div class="abs" style="left:63px;top:64px;width:160px">
      <h3 class="h-service">Tormalux Support</h3>
      <p class="body-text" style="margin-top:6px">Maecenas aliquet velit vel turpis Mauris neque metus malesuada nec ultricies sit amet porttitor</p>
      <p class="body-text" style="margin-top:6px">Aed nulla In ullamcorper est eget tempor cursus neque mi consectetuer mi a ultricies massa est sed nisl Class aptent taciti sociosqu ad litora torquent per</p>
      <span class="btn-outline" style="margin-top:8px">READ MORE</span>
    </div>
    <div class="abs circle-photo" style="left:247px;top:45px;width:130px;height:130px"><div class="photo" role="img" aria-label="Smiling support agent with headset in an office"></div></div>
  </section>

  <section class="block" style="top:801px;height:183px;background:var(--grey-band)">
    <div class="abs circle-photo" style="left:71px;top:26px;width:133px;height:133px"><div role="img" aria-label="Server rack with network cables" style="background:radial-gradient(circle,#5aa9e6,#1e3f8a)"></div></div>
    <div class="abs" style="left:239px;top:40px;width:160px">
      <h3 class="h-service">Tormalux Hosting</h3>
      <p class="body-text" style="margin-top:6px">Maecenas aliquet velit vel turpis Mauris neque metus malesuada nec ultricies sit amet porttitor</p>
      <p class="body-text" style="margin-top:6px">Aed nulla In ullamcorper est eget tempor cursus neque mi consectetuer mi a ultricies massa est sed nisl Class aptent taciti sociosqu ad litora torquent per</p>
      <span class="btn-outline" style="margin-top:8px">READ MORE</span>
    </div>
  </section>

  <section class="block" style="top:984px;height:174px">
    <div class="abs" style="left:69px;top:37px;width:160px">
      <h3 class="h-service">Tormalux Customisation</h3>
      <p class="body-text" style="margin-top:6px">Maecenas aliquet velit vel turpis Mauris neque metus malesuada nec ultricies sit amet porttitor</p>
      <p class="body-text" style="margin-top:6px">Aed nulla In ullamcorper est eget tempor cursus neque mi consectetuer mi a ultricies massa est sed nisl Class aptent taciti sociosqu ad litora torquent per</p>
      <span class="btn-outline" style="margin-top:8px">READ MORE</span>
    </div>
    <div class="abs circle-photo" style="left:247px;top:15px;width:134px;height:134px"><div class="photo" role="img" aria-label="Call centre agent with headset and glasses at his desk" style="background:linear-gradient(120deg,#c9ced6,#7d8a9c)"></div></div>
  </section>

  <section class="block quote">
    <h2 class="section-title" style="position:absolute;top:16px;width:100%;font-weight:500">Request a Quote</h2>
    <div class="field" style="left:102px;top:41px;width:123px">Name</div>
    <div class="field" style="left:230px;top:41px;width:123px">Email address</div>
    <div class="field" style="left:102px;top:61px;width:123px">Phone</div>
    <div class="field" style="left:230px;top:61px;width:123px;display:flex;justify-content:space-between">Select Service<svg width="6" height="6" viewBox="0 0 6 6"><path d="M1 2l2 2 2-2" fill="none" stroke="#666"/></svg></div>
    <div class="field" style="left:102px;top:81px;width:251px;height:33px">Message</div>
    <div class="abs submit" style="left:194px;top:122px;width:68px;height:18px">SUBMIT NOW</div>
  </section>

  <footer class="block footer" style="top:1315px;height:118px">
    <div class="abs f-brand" style="left:68px;top:26px"><span class="brand-dot"></span>Dialwise</div>
    <div class="abs f-col" style="left:147px;top:30px"><h4>Company</h4><p>Home</p><p>About Us</p><p>Why Us</p></div>
    <div class="abs f-col" style="left:203px;top:30px"><h4>Resources</h4><p>Our Services</p><p>Team</p><p>Blogs</p></div>
    <div class="abs f-col" style="left:266px;top:28px"><h4>Contact Info</h4><p>☎ 02 5550 1847</p><p>✉ hello@dialwise.example</p></div>
    <div class="abs f-col" style="left:349px;top:28px"><h4>Follow Us</h4><p>▪ Chirpline</p><p>▪ Friendsy</p><p>▪ Worknet</p></div>
  </footer>
  <div class="block bar" style="top:1433px;height:22px">© 2018 Company Name. All right reserved. Term of Use<span class="tag">X14</span></div>
</main>

<!-- CONTACT PAGE -->
<main class="page page--contact">
  <header class="block nav" style="height:33px">
    <div class="brand"><span class="brand-dot"></span>Dialwise</div>
    <nav class="menu" style="left:180px;height:33px"><span>Home</span><span>About Us</span><span>Our Services</span><span>Blogs</span><span class="active">Contact Us</span></nav>
  </header>
  <section class="block photo" style="top:33px;height:138px;background:linear-gradient(120deg,#8a9aa8,#c7b7a4 55%,#e6ddd2)" role="img" aria-label="Hands typing on a laptop beside a cup of tea">
    <div class="abs" style="left:0;top:55px;width:200px;height:34px;background:rgba(32,173,160,.92);border-radius:0 17px 17px 0;color:#fff;font-size:12px;line-height:34px;padding-left:74px">Contact Us</div>
    <div class="abs scroll-tab" style="top:124px"><div class="abs scroll-mouse"></div></div>
  </section>
  <section class="block" style="top:171px;height:185px">
    <div class="abs" style="left:69px;top:26px;width:115px">
      <h2 style="font-size:13px;font-weight:500">Contact Us</h2>
      <p class="contact-label" style="margin-top:10px">ADDRESS</p>
      <p class="contact-val">48 Harbour Lane Suite 3<br>Perth WA 6000</p>
      <p class="contact-label" style="margin-top:9px">PHONE</p>
      <p class="contact-val">02 5550 1847</p>
      <p class="contact-label" style="margin-top:9px">EMAIL US</p>
      <p class="contact-val">hello@dialwise.example</p>
    </div>
    <div class="abs quote-box">
      <h3>REQUEST A QUOTE</h3>
      <div class="qfield" style="left:12px;top:28px;width:87px">Name</div>
      <div class="qfield" style="left:101px;top:28px;width:87px">Phone</div>
      <div class="qfield" style="left:12px;top:43px;width:87px">Address</div>
      <div class="qfield" style="left:101px;top:43px;width:87px">Email</div>
      <div class="qfield" style="left:12px;top:58px;width:176px;height:35px">Message</div>
      <div class="abs submit" style="left:12px;top:97px;width:56px;height:12px;line-height:12px;border-radius:2px;font-size:4.5px">SUBMIT NOW</div>
    </div>
  </section>
  <footer class="block footer" style="top:356px;height:120px">
    <div class="abs f-brand" style="left:70px;top:30px"><span class="brand-dot"></span>Dialwise</div>
    <div class="abs f-col" style="left:149px;top:32px"><h4>Company</h4><p>Home</p><p>About Us</p><p>Why Us</p></div>
    <div class="abs f-col" style="left:205px;top:32px"><h4>Resources</h4><p>Our Services</p><p>Team</p><p>Blogs</p></div>
    <div class="abs f-col" style="left:269px;top:30px"><h4>Contact Info</h4><p>☎ 02 5550 1847</p><p>✉ hello@dialwise.example</p></div>
    <div class="abs f-col" style="left:352px;top:30px"><h4>Follow Us</h4><p>▪ Chirpline</p><p>▪ Friendsy</p><p>▪ Worknet</p></div>
  </footer>
  <div class="block bar" style="top:476px;height:29px;line-height:22px">© 2018 Company Name. All right reserved. Term of Use<span class="tag" style="top:4px">X14</span></div>
</main>

</div>
</body>
</html>
```